Accountability Project Graphics

I want to create 10 social media graphics (new Instagram size 4:5 (1080 x 1350 pixels) focusing on our Quilvo Accountability App, using any of the 3 pictures attached. Use the attached pics only, NO RANDOM STOCK PHOTOGRAPHY. For the color scheme, use the landing page colors/fonts (attached).
You can add any of the 3 photos attached but I mainly need BOLD text that includes these headlines and sub-headlines on them.
Please NOTE for all the headlines below, also add this sub-headline on each graphic:
Stay Consistent with RT in Your Pocket!
Here are the headlines:
• Stop Starting Over Every Monday
• You don't need more willpower. You need more support
• Built for women who are tired of doing this alone
• When Motivation Fades, RT Checks In
• The Support System You've Been Missing
• Support When Motivation Disappears
• What if RT Checked in Every Day?
• The Missing Piece Isn't Another Diet
• Eat the food you love. Stay accountable every day.
• One Bad Meal Doesn't Mean You Failed
women over 40 trying to lose weight

```html
<!DOCTYPE html>
<html lang="en">
<head>
<meta charset="utf-8">
<title>Quilvo Accountability Graphics</title>
<link rel="stylesheet" href="https://fonts.googleapis.com/css2?family=DM+Serif+Display:ital@0;1&family=Inter:wght@600;700&display=swap">
<style>
  :root{
    --plum:#2b0f36;
    --purple:#4b1a52;
    --pink:#d8407f;
    --pink-deep:#b82a66;
    --blush:#fbe4ea;
    --blush-2:#f7cfdc;
    --cream:#fff4f5;
    --navy:#1d2338;
    --black:#000;
  }
  *{margin:0;padding:0;box-sizing:border-box}
  html,body{width:1200px;height:1124px;overflow:hidden;background:var(--black)}
  .board{position:relative;width:1200px;height:1124px}
  .tile{position:absolute;width:298px;height:372px;overflow:hidden;
    background:radial-gradient(circle at 70% 30%,var(--cream),var(--blush) 55%,var(--blush-2));}
  .swoosh{position:absolute;inset:0;width:298px;height:372px}
  .photo{position:absolute;background:linear-gradient(160deg,#3a3f58,var(--navy) 60%,#141829)}
  .photo.portrait{border-radius:140px 140px 0 0}
  .photo.pair{background:linear-gradient(160deg,#efe4e4,#6d7a98 45%,#2d3a5c);border-radius:18px}
  .photo.hug{background:linear-gradient(150deg,#d9b7a8,#e05b94 45%,#e8f0c6 85%);border-radius:18px}
  .photo.round{border-radius:50%;border:3px solid #fff}
  .photo.card{border:3px solid #fff;border-radius:6px}
  .headline{position:absolute;z-index:2;font-family:"DM Serif Display",serif;color:var(--plum);line-height:.92;letter-spacing:-.5px}
  .headline .accent{color:var(--pink)}
  .headline.italic{font-style:italic}
  .ribbon{position:absolute;z-index:2;background:linear-gradient(90deg,var(--pink-deep),var(--pink));color:#fff;
    font-family:"DM Serif Display",serif;padding:4px 10px;line-height:1.1;transform:rotate(-3deg);
    box-shadow:0 2px 4px rgba(75,26,82,.3)}
  .ribbon.italic{font-style:italic}
  .sub-sans{position:absolute;z-index:2;font-family:"Inter",sans-serif;font-weight:700;color:var(--plum)}
  .pill{position:absolute;z-index:2;background:var(--pink);color:#fff;font-family:"Inter",sans-serif;font-weight:600;
    font-size:5.5px;border-radius:8px;padding:4px 10px}
</style>
</head>
<body>
<main class="board">

  <!-- When Motivation Fades -->
  <section class="tile" style="left:0;top:0">
    <svg class="swoosh" viewBox="0 0 298 372"><path d="M0 300 C80 250 200 280 298 230 V372 H0Z" fill="var(--purple)"/><path d="M0 320 C90 270 200 300 298 250 V265 C200 315 90 290 0 340Z" fill="var(--pink)"/></svg>
    <div class="photo portrait" role="img" aria-label="Coach smiling, hand on hip" style="left:165px;top:25px;width:135px;height:347px"></div>
    <h2 class="headline" style="left:14px;top:20px;font-size:33px">When<br><span class="accent">Motivation</span><br>Fades,<br><span class="accent">RT</span><br>Checks In</h2>
    <div class="ribbon" style="left:10px;top:192px;width:165px;font-size:12px">Stay Consistent<br>with RT in Your Pocket!</div>
    <div class="photo hug round" role="img" aria-label="Coach hugging a client" style="left:8px;top:238px;width:96px;height:96px"></div>
    <div class="photo pair round" role="img" aria-label="Coach laughing with a client" style="left:85px;top:272px;width:100px;height:100px"></div>
  </section>

  <!-- Built for women -->
  <section class="tile" style="left:300px;top:0">
    <svg class="swoosh" viewBox="0 0 298 372"><path d="M0 290 C60 320 120 300 160 340 L140 372 H0Z" fill="var(--purple)"/><path d="M100 372 C150 330 230 340 298 300 V372Z" fill="var(--pink)"/></svg>
    <h2 class="headline" style="left:32px;top:22px;font-size:27px">Built for<br>women who<br>are tired of<br><span class="accent">doing this<br>alone</span></h2>
    <div class="ribbon" style="left:22px;top:150px;width:175px;font-size:8px">Stay Consistent with RT in Your Pocket!</div>
    <div class="photo portrait" role="img" aria-label="Coach smiling, hand on hip" style="left:195px;top:122px;width:103px;height:250px"></div>
    <div class="photo pair" role="img" aria-label="Coach laughing with a client" style="left:20px;top:175px;width:175px;height:175px"></div>
  </section>

  <!-- Support System -->
  <section class="tile" style="left:600px;top:0">
    <svg class="swoosh" viewBox="0 0 298 372"><path d="M0 330 C100 300 200 340 298 310 V372 H0Z" fill="var(--purple)"/><circle cx="265" cy="150" r="45" fill="var(--purple)" opacity=".8"/></svg>
    <div class="photo pair" role="img" aria-label="Coach laughing with a client" style="left:45px;top:10px;width:180px;height:180px"></div>
    <div class="photo portrait" role="img" aria-label="Coach smiling, hand on hip" style="left:190px;top:145px;width:108px;height:227px"></div>
    <h2 class="headline" style="left:25px;top:165px;font-size:29px">The<br>Support<br>System<br><span class="accent">You’ve Been<br>Missing</span></h2>
    <div class="ribbon italic" style="left:22px;top:308px;width:190px;font-size:9px">Stay Consistent with RT in Your Pocket!</div>
  </section>

  <!-- Missing Piece -->
  <section class="tile" style="left:900px;top:0">
    <svg class="swoosh" viewBox="0 0 298 372"><path d="M0 220 C60 250 160 260 298 200 V230 C170 280 60 260 0 245Z" fill="var(--pink)"/></svg>
    <div class="photo portrait" role="img" aria-label="Coach smiling, hand on hip" style="left:130px;top:5px;width:168px;height:235px"></div>
    <div class="photo hug round" role="img" aria-label="Coach hugging a client" style="left:12px;top:6px;width:98px;height:98px"></div>
    <div class="photo pair round" role="img" aria-label="Coach laughing with a client" style="left:18px;top:115px;width:115px;height:115px"></div>
    <h2 class="headline" style="left:28px;top:252px;font-size:34px">The Missing<br>Piece <span class="accent" style="font-style:italic">Isn’t</span><br><span class="accent" style="font-style:italic">Another</span> Diet</h2>
    <p class="sub-sans" style="left:31px;top:355px;font-size:8.5px">Stay Consistent with <span style="color:var(--pink)">RT</span> in Your Pocket!</p>
  </section>

  <!-- One Bad Meal -->
  <section class="tile" style="left:0;top:374px">
    <svg class="swoosh" viewBox="0 0 298 372"><path d="M0 350 C120 360 220 330 298 290 V372 H0Z" fill="var(--purple)"/><path d="M0 340 C120 350 220 320 298 270 V290 C220 340 120 362 0 355Z" fill="var(--pink)"/></svg>
    <div class="photo portrait" role="img" aria-label="Coach smiling, hand on hip" style="left:165px;top:25px;width:133px;height:347px"></div>
    <h2 class="headline italic" style="left:22px;top:26px;font-size:30px">One Bad<br>Meal<br><span class="accent">Doesn’t<br>Mean You<br>Failed</span></h2>
    <div class="ribbon" style="left:12px;top:168px;width:145px;font-family:'Inter',sans-serif;font-weight:600;font-size:9px;text-align:center">Stay Consistent with<br>RT in Your Pocket!</div>
    <div class="photo hug round" role="img" aria-label="Coach hugging a client" style="left:14px;top:198px;width:108px;height:108px"></div>
    <div class="photo pair round" role="img" aria-label="Coach laughing with a client" style="left:68px;top:250px;width:118px;height:118px"></div>
  </section>

  <!-- Stop Starting Over -->
  <section class="tile" style="left:300px;top:374px">
    <svg class="swoosh" viewBox="0 0 298 372"><path d="M0 320 C80 290 180 330 298 300 V372 H0Z" fill="var(--purple)"/><path d="M0 300 C90 270 190 310 298 270 V290 C190 330 90 290 0 318Z" fill="var(--pink)"/><path d="M240 0 H298 V70Z" fill="var(--purple)"/></svg>
    <div style="position:absolute;left:12px;top:45px;width:160px;height:170px;background:var(--cream);border-radius:16px"></div>
    <div class="photo portrait" role="img" aria-label="Coach smiling, hand on hip" style="left:160px;top:55px;width:138px;height:317px"></div>
    <h2 class="headline" style="left:26px;top:52px;font-size:35px">Stop<br>Starting<br>Over<br><span class="accent">Every</span><br>Monday</h2>
    <div class="ribbon italic" style="left:12px;top:225px;width:158px;font-size:12px;text-align:center">Stay Consistent with<br>RT in Your Pocket!</div>
  </section>

  <!-- Willpower -->
  <section class="tile" style="left:600px;top:374px">
    <svg class="swoosh" viewBox="0 0 298 372"><path d="M120 372 C180 330 240 340 298 300 V372Z" fill="var(--purple)"/><path d="M0 20 V150 C20 100 20 60 0 20Z" fill="var(--blush-2)"/></svg>
    <h2 class="headline" style="left:50px;top:20px;font-size:23.5px">You don’t need<br>more willpower.<br>You need<br><span class="accent" style="font-size:32px">more support</span></h2>
    <div class="ribbon" style="left:40px;top:130px;width:240px;font-size:9.5px;text-align:center">Stay Consistent with RT in Your Pocket!</div>
    <div class="photo hug" role="img" aria-label="Coach hugging a client" style="left:0;top:155px;width:180px;height:217px;border-radius:0 60px 0 0"></div>
    <div class="photo pair round" role="img" aria-label="Coach laughing with a client" style="left:170px;top:158px;width:122px;height:122px"></div>
    <div class="photo portrait" role="img" aria-label="Coach smiling, hand on hip" style="left:210px;top:245px;width:88px;height:127px"></div>
  </section>

  <!-- Eat the food -->
  <section class="tile" style="left:900px;top:374px">
    <svg class="swoosh" viewBox="0 0 298 372"><circle cx="265" cy="120" r="95" fill="var(--purple)"/><path d="M0 340 C100 380 200 320 298 250 V280 C200 350 100 390 0 360Z" fill="var(--pink)"/></svg>
    <div class="photo portrait" role="img" aria-label="Coach smiling, hand on hip" style="left:188px;top:30px;width:110px;height:342px"></div>
    <h2 class="headline" style="left:18px;top:22px;font-size:33px">Eat the<br>food<br><span class="accent">you love.</span><br><span class="accent" style="font-size:26px">Stay<br>accountable</span><br><span style="font-size:26px">every day.</span></h2>
    <div class="pill" style="left:18px;top:214px">✦ Stay Consistent with RT in Your Pocket!</div>
    <div class="photo hug card" role="img" aria-label="Coach hugging a client" style="left:5px;top:240px;width:88px;height:95px;transform:rotate(-4deg)"></div>
    <div class="photo pair card" role="img" aria-label="Coach laughing with a client" style="left:85px;top:245px;width:90px;height:100px;transform:rotate(5deg)"></div>
  </section>

  <!-- Support When Motivation Disappears -->
  <section class="tile" style="left:300px;top:748px">
    <svg class="swoosh" viewBox="0 0 298 372"><path d="M0 0 H45 C20 60 20 120 0 160Z" fill="var(--purple)"/><path d="M230 300 C260 320 280 310 298 290 V372 H200Z" fill="var(--purple)"/></svg>
    <div class="photo hug" role="img" aria-label="Coach hugging a client" style="left:20px;top:0;width:215px;height:205px;border-radius:0 0 90px 40px"></div>
    <div class="photo pair card" role="img" aria-label="Coach laughing with a client" style="left:207px;top:52px;width:82px;height:88px;transform:rotate(3deg)"></div>
    <div class="photo card" role="img" aria-label="Coach smiling, hand on hip" style="left:210px;top:145px;width:80px;height:110px;transform:rotate(-2deg)"></div>
    <h2 class="headline" style="left:18px;top:208px;font-size:31px">Support<br>When<br><span class="accent">Motivation</span><br>Disappears</h2>
    <div class="ribbon italic" style="left:18px;top:332px;width:215px;font-size:11px;text-align:center">Stay Consistent with RT in Your Pocket!</div>
  </section>

  <!-- What if RT -->
  <section class="tile" style="left:600px;top:748px">
    <svg class="swoosh" viewBox="0 0 298 372"><circle cx="250" cy="80" r="80" fill="var(--pink)" opacity=".35"/><path d="M0 320 C100 290 200 310 298 260 V372 H0Z" fill="var(--purple)"/><path d="M0 300 C100 280 200 300 298 250 V268 C200 320 100 300 0 318Z" fill="var(--pink)"/></svg>
    <div class="photo portrait" role="img" aria-label="Coach smiling, hand on hip" style="left:172px;top:45px;width:126px;height:327px"></div>
    <h2 class="headline" style="left:15px;top:28px;font-size:31px;text-align:center">What if RT<br><span class="accent">Checked in</span><br>Every Day?</h2>
    <p class="sub-sans" style="left:21px;top:138px;font-size:9.5px;line-height:1.2">Stay Consistent with<br><span style="color:var(--pink)">RT in Your Pocket!</span></p>
    <div class="photo hug card" role="img" aria-label="Coach hugging a client" style="left:10px;top:165px;width:90px;height:115px;transform:rotate(-4deg)"></div>
    <div class="photo pair card" role="img" aria-label="Coach laughing with a client" style="left:78px;top:200px;width:95px;height:115px;transform:rotate(3deg)"></div>
  </section>

</main>
</body>
</html>
```